Harbor Crestline (Business Card Design)

Need business cards designed. Something modern, chic, and sleek. Mabye the back of the card should be the navy blue that is in the logo and then just the logo on the back.

Target Market(s)

Those in the hotel, office, and renovation industry

Contact Information for Business Card

1. Logo 2. Dorian Fenwick 3. CEO/Founder 4. Phone: (833) HarbCre / (833) 427-2731 5. Email: dorian@theharborcrestline.com 6. Website: www.theharborcrestline.com

Font styles to use
Other font styles liked:
• Look at the logo font and base the font for everything else off of that.

Colors
0054AA
0677BA
7BADD7
CADEEF
E8F1F8

Requirements
Must have
• Colors that are associated in the logo
Nice to have
• Sleek modern clean and chic design.

```html
<!DOCTYPE html>
<html lang="en">
<head>
<meta charset="utf-8">
<title>Harbor Crestline – Business Card</title>
<link href="https://fonts.googleapis.com/css2?family=Montserrat:wght@500;600;700;800&family=Open+Sans:wght@400;600&display=swap" rel="stylesheet">
<style>
  :root {
    --stage: #222222;
    --navy: #0d1a40;
    --navy-deep: #0a1533;
    --navy-emboss: #1d2c5e;
    --gold: #d1a84b;
    --white: #ffffff;
    --text-soft: #e9edf5;
  }
  * { box-sizing: border-box; margin: 0; padding: 0; }
  html, body {
    width: 1200px; height: 780px; overflow: hidden;
    background: var(--stage);
  }
  .stage {
    width: 1200px; height: 780px;
    display: flex; align-items: center; justify-content: center; gap: 40px;
  }
  .card {
    position: relative;
    width: 560px; height: 320px;
    background: var(--navy);
    border-radius: 18px;
    border: 3px solid var(--gold);
    overflow: hidden;
    box-shadow: 0 14px 30px rgba(0,0,0,.55);
  }

  /* Back side */
  .card-back { display: flex; align-items: center; justify-content: center; }
  .back-wordmark {
    display: flex; align-items: center; gap: 14px;
    font-family: "Montserrat", sans-serif; font-weight: 800;
    font-size: 34px; letter-spacing: 4px; text-transform: uppercase;
    color: var(--navy-emboss);
  }
  .back-wordmark .mark-square {
    width: 22px; height: 22px; background: var(--navy-emboss);
  }

  /* Front side */
  .brand {
    position: absolute; left: 34px; top: 98px; width: 210px;
    display: flex; flex-direction: column; align-items: flex-start; gap: 10px;
  }
  .brand .mark-square { width: 16px; height: 16px; background: var(--gold); }
  .brand-name {
    font-family: "Montserrat", sans-serif; font-weight: 700;
    font-size: 27px; line-height: 1.1; letter-spacing: 3px;
    text-transform: uppercase; color: var(--white);
  }
  .divider {
    position: absolute; left: 262px; top: 48px;
    width: 2px; height: 168px; background: var(--white);
  }
  .details { position: absolute; left: 286px; top: 48px; right: 20px; }
  .person-name {
    font-family: "Montserrat", sans-serif; font-weight: 800;
    font-size: 26px; line-height: 1; color: var(--white);
  }
  .person-name .first { color: var(--gold); }
  .person-title {
    margin-top: 5px;
    font-family: "Open Sans", sans-serif; font-weight: 600;
    font-size: 13px; color: var(--white);
  }
  .address {
    margin-top: 18px;
    font-family: "Open Sans", sans-serif; font-size: 11px; line-height: 1.45;
    color: var(--text-soft);
  }
  .contact-list { margin-top: 14px; list-style: none; }
  .contact-list li {
    display: flex; align-items: center; gap: 7px;
    font-family: "Open Sans", sans-serif; font-size: 11px; line-height: 1.6;
    color: var(--text-soft);
  }
  .contact-list svg { width: 11px; height: 11px; flex: none; }

  .band-gold {
    position: absolute; left: 0; width: 290px; bottom: 24px; height: 14px;
    background: var(--gold);
  }
  .band-white {
    position: absolute; left: 322px; right: 0; bottom: 48px; height: 14px;
    background: var(--white);
  }
  .band-joint {
    position: absolute; left: 296px; bottom: 32px; width: 20px; height: 20px;
    border: 2px solid var(--white); background: var(--navy);
  }
</style>
</head>
<body>
<main class="stage">

  <section class="card card-back" aria-label="Card back">
    <div class="back-wordmark">
      <span class="mark-square"></span>
      <span>Harbor Crestline</span>
    </div>
  </section>

  <section class="card card-front" aria-label="Card front">
    <div class="brand">
      <span class="mark-square"></span>
      <span class="brand-name">Harbor<br>Crestline</span>
    </div>

    <div class="divider"></div>

    <div class="details">
      <h1 class="person-name"><span class="first">Dorian</span> Fenwick</h1>
      <p class="person-title">CEO/Founder</p>
      <p class="address">1420 Marlow Ave<br>Suite 210, Ashby, MD 20914</p>
      <ul class="contact-list">
        <li>
          <svg viewBox="0 0 24 24" aria-hidden="true"><path fill="#d1a84b" d="M6.6 10.8a15 15 0 0 0 6.6 6.6l2.2-2.2a1 1 0 0 1 1-.25 11.4 11.4 0 0 0 3.6.57 1 1 0 0 1 1 1V20a1 1 0 0 1-1 1A17 17 0 0 1 3 4a1 1 0 0 1 1-1h3.5a1 1 0 0 1 1 1c0 1.25.2 2.46.57 3.6a1 1 0 0 1-.25 1z"/></svg>
          (833) HarbCre / (833) 427-2731
        </li>
        <li>
          <svg viewBox="0 0 24 24" aria-hidden="true"><circle cx="12" cy="12" r="9" fill="none" stroke="#d1a84b" stroke-width="2"/><ellipse cx="12" cy="12" rx="4" ry="9" fill="none" stroke="#d1a84b" stroke-width="2"/><line x1="3" y1="12" x2="21" y2="12" stroke="#d1a84b" stroke-width="2"/></svg>
          www.theharborcrestline.com
        </li>
        <li>
          <svg viewBox="0 0 24 24" aria-hidden="true"><rect x="3" y="5" width="18" height="14" rx="1.5" fill="none" stroke="#d1a84b" stroke-width="2"/><path d="M3.5 6l8.5 7 8.5-7" fill="none" stroke="#d1a84b" stroke-width="2"/></svg>
          dorian@theharborcrestline.com
        </li>
      </ul>
    </div>

    <div class="band-gold"></div>
    <div class="band-joint"></div>
    <div class="band-white"></div>
  </section>

</main>
</body>
</html>
```